Meadow Kr Circle (company name is Meadow Kr Circle LLP)

management of homestay, hospitality something similar with https://www.dorvika.example

Target Market(s)

johor bahru market (Malaysia)

Contact Information for Business Card

Meadow Circle KR LLP

Logo Text

eyes catching, attractive, amazing, Nice, jaw dropping for design

Coding

Coded - Design and coding required

Number of Pages Required

5+ page

Colors

Designer to choose colors to be used in the design.

Requirements
Must have
• please change the short term proposal to our company logo and change the name from dorvika to meadow KR Circle LLP
• thanks
Nice to have
• please let me have eyes catching , jaw dropping design

```html
<!DOCTYPE html>
<html lang="en">
<head>
<meta charset="utf-8">
<title>Meadow Kr Circle — Rent Management</title>
<link rel="stylesheet" href="https://fonts.googleapis.com/css2?family=Montserrat:wght@400;500;600;700;800&family=Open+Sans:wght@400;600&display=swap">
<style>
:root{
  --red:#ee3a46;
  --ink:#1e1e1e;
  --text:#555;
  --muted:#c9c9c9;
  --soft:#f4f1f1;
  --line:#e2dede;
  --white:#fff;
  --footer:#262626;
  --blue:#1d4b8c;
}
*{margin:0;padding:0;box-sizing:border-box}
html,body{width:1200px;height:4018px;overflow:hidden}
body{position:relative;background:var(--white);font-family:"Open Sans",Arial,sans-serif;color:var(--text)}
.abs{position:absolute}

/* header */
.site-header{top:0;left:0;width:1200px;height:118px;background:var(--white)}
.brand{left:145px;top:36px;font-family:"Montserrat",Arial,sans-serif;font-weight:500;font-size:32px;color:var(--ink)}
.callout{left:733px;top:26px;display:flex;align-items:center;gap:8px}
.callout .dot{width:30px;height:30px;border-radius:50%;background:var(--red);display:flex;align-items:center;justify-content:center}
.callout small{display:block;font-size:9px;font-weight:600;color:var(--ink);letter-spacing:.5px}
.callout strong{display:block;font-family:"Montserrat",Arial,sans-serif;font-size:24px;font-weight:500;color:var(--ink);line-height:1}
.socials{left:955px;top:30px;display:flex;gap:8px}
.socials span{width:26px;height:26px;border-radius:50%;background:var(--blue)}
.main-nav{left:480px;top:76px;display:flex;gap:8px;font-family:"Montserrat",Arial,sans-serif;font-size:14px;font-weight:500;color:var(--ink)}
.main-nav a{padding:6px 10px;color:inherit;text-decoration:none}
.main-nav a.active{background:var(--red);color:var(--white)}

/* hero */
.hero{top:118px;left:0;width:1200px;height:602px;background:linear-gradient(180deg,#d8d2c8 0%,#bfb3a3 45%,#8a6546 80%,#6b4a33 100%)}
.hero-arrow{top:400px;width:22px;height:36px;background:#222;display:flex;align-items:center;justify-content:center}
.hero-copy{top:495px;left:0;width:1200px;text-align:center;color:var(--white)}
.hero-copy h1{font-family:"Montserrat",Arial,sans-serif;font-weight:800;font-size:44px;letter-spacing:.5px;text-shadow:0 2px 6px rgba(0,0,0,.35)}
.hero-copy p{font-family:"Montserrat",Arial,sans-serif;font-weight:700;font-size:27px;margin-top:2px;text-shadow:0 2px 6px rgba(0,0,0,.35)}
.btn{display:inline-block;background:var(--red);color:var(--white);font-family:"Montserrat",Arial,sans-serif;font-weight:700;text-transform:uppercase;text-decoration:none}
.hero-copy .btn{margin-top:20px;font-size:18px;padding:14px 30px;box-shadow:0 3px 8px rgba(0,0,0,.3)}

/* welcome */
.welcome-photo{left:175px;top:777px;width:372px;height:400px;background:linear-gradient(180deg,#c9d4dc 0%,#a7a8a2 40%,#6f8a4a 85%,#4d6a35 100%)}
.welcome-text{left:615px;top:796px;width:440px}
.rule{width:36px;height:4px;background:var(--red);margin-bottom:16px}
.welcome-text .eyebrow{font-family:"Montserrat",Arial,sans-serif;font-size:16px;font-weight:500;color:var(--ink)}
.welcome-text h2{font-family:"Montserrat",Arial,sans-serif;font-size:38px;font-weight:500;color:var(--ink);margin:4px 0 24px}
.welcome-text p{font-size:14px;line-height:1.5;color:#444;margin-bottom:18px}
.welcome-text .btn{font-size:12px;padding:8px 20px;margin-top:4px}

/* services */
.services{top:1238px;left:0;width:1200px;height:532px;background:var(--soft)}
.section-title{width:1200px;left:0;text-align:center}
.section-title .rule{margin:0 auto 18px}
.section-title h2{font-family:"Montserrat",Arial,sans-serif;font-size:34px;font-weight:500;color:var(--ink)}
.service{width:310px;text-align:center;top:210px}
.service svg{display:block;margin:0 auto 30px}
.service h3{font-family:"Montserrat",Arial,sans-serif;font-size:17px;font-weight:600;color:var(--ink);line-height:1.4;margin-bottom:14px}
.service p{font-size:13px;line-height:1.5;color:#444}
.divider{top:200px;width:1px;height:200px;background:#ddd}

/* steps */
.steps-title{top:1840px}
.steps-title p{font-size:15px;color:#333;margin-top:10px;line-height:1.45}
.step{top:2090px;width:200px;height:250px;background:var(--white);border:1px solid var(--line);border-top:4px solid var(--red);padding:34px 24px;text-align:center}
.step-num{font-family:"Montserrat",Arial,sans-serif;font-size:44px;font-weight:700;color:var(--muted);line-height:1}
.step .rule{margin:18px auto}
.step-label{font-family:"Montserrat",Arial,sans-serif;font-size:16px;color:#333;line-height:1.35}

/* packages */
.packages{top:2520px;left:0;width:1200px;height:608px;background:var(--soft)}
.card{top:160px;width:286px;height:305px;background:var(--white);box-shadow:0 2px 10px rgba(0,0,0,.08);padding:42px 30px 42px 38px}
.card .price{font-family:"Montserrat",Arial,sans-serif;font-size:25px;font-weight:600;color:var(--red)}
.card h3{font-family:"Montserrat",Arial,sans-serif;font-size:17px;font-weight:600;color:var(--ink);margin:22px 0 12px}
.card ul{list-style:none;font-size:12px;color:#333;line-height:1.75;white-space:nowrap}
.card li::before{content:"";display:inline-block;width:0;height:0;border-left:5px solid var(--red);border-top:4px solid transparent;border-bottom:4px solid transparent;margin-right:10px}
.packages .btn{top:510px;left:510px;font-size:12px;padding:10px 22px}

/* banner */
.banner{top:3128px;left:0;width:1200px;height:492px;background:linear-gradient(180deg,#3b3530 0%,#4e4236 45%,#3a2e24 100%)}
.banner-copy{left:0;width:1200px;text-align:center;color:var(--white)}
.banner-copy h2{font-family:"Montserrat",Arial,sans-serif;font-size:35px;font-weight:700}
.banner-copy p{font-family:"Montserrat",Arial,sans-serif;font-size:21px;font-weight:600;line-height:1.5;margin-top:14px}
.banner-copy .btn{margin-top:38px;font-size:15px;padding:11px 26px}

/* footer */
.footer-line{top:3620px;left:0;width:1200px;height:5px;background:var(--red)}
.site-footer{top:3625px;left:0;width:1200px;height:393px;background:var(--footer);color:#ddd}
.site-footer .brand{top:130px;left:148px;color:var(--white);font-size:31px}
.f-col{top:70px;font-size:11px;line-height:1.7}
.f-col h4{font-family:"Montserrat",Arial,sans-serif;font-size:11px;font-weight:700;color:var(--white);letter-spacing:.3px;margin-bottom:24px}
.f-row{display:flex;gap:12px;margin-bottom:14px}
.f-row svg{flex:none;margin-top:3px}
.social-row{display:flex;align-items:center;gap:12px;margin-bottom:16px}
.social-row span{width:24px;height:24px;border-radius:50%;background:var(--blue)}
.f-rule{top:278px;left:145px;width:910px;height:1px;background:#3a3a3a}
.copyright{top:333px;left:0;width:1200px;text-align:center;font-size:11px;color:#ccc}
</style>
</head>
<body>

<header class="site-header abs">
  <div class="brand abs">Meadow Kr Circle</div>
  <div class="callout abs">
    <span class="dot"><svg width="16" height="16" viewBox="0 0 24 24"><path d="M6.6 10.8a15 15 0 0 0 6.6 6.6l2.2-2.2c.3-.3.7-.4 1-.2 1.1.4 2.3.6 3.6.6.6 0 1 .4 1 1V20c0 .6-.4 1-1 1A17 17 0 0 1 3 4c0-.6.4-1 1-1h3.5c.6 0 1 .4 1 1 0 1.3.2 2.5.6 3.6.1.3 0 .7-.2 1z" fill="#fff"/></svg></span>
    <div><small>CALL US NOW</small><strong>555.014.2040</strong></div>
  </div>
  <div class="socials abs"><span></span><span></span><span></span></div>
  <nav class="main-nav abs">
    <a class="active" href="#">Home</a><a href="#">About us</a><a href="#">Services</a><a href="#">Explore the Place</a><a href="#">Blog</a><a href="#">Contact Us</a>
  </nav>
</header>

<section class="hero abs" role="img" aria-label="Bright living room with white sofas, fireplace and kitchen counter"></section>
<div class="hero-arrow abs" style="left:0"><svg width="10" height="14"><path d="M8 1 2 7l6 6" stroke="#fff" stroke-width="2" fill="none"/></svg></div>
<div class="hero-arrow abs" style="left:1178px"><svg width="10" height="14"><path d="M2 1l6 6-6 6" stroke="#fff" stroke-width="2" fill="none"/></svg></div>
<div class="hero-copy abs">
  <h1>RENT MANAGEMENT</h1>
  <p>Maximize your rental income</p>
  <a class="btn" href="#">Book now</a>
</div>

<div class="welcome-photo abs" role="img" aria-label="Family walking towards a brick house"></div>
<div class="welcome-text abs">
  <div class="rule"></div>
  <div class="eyebrow">WELCOME TO</div>
  <h2>Meadow Kr Circle</h2>
  <p>We are a short-term rental management and provides hospitality services to help property owners maximise their rental income.</p>
  <p>Our goal is to help you reap the most from your rental income without you having to do any of the hard work such as handle all the particular renting problems on StayNest, RoomBay, cleaning and dealing with tenants and guests</p>
  <a class="btn" href="#">Read more</a>
</div>

<section class="services abs">
  <div class="section-title abs" style="top:80px"><div class="rule"></div><h2>Our Services</h2></div>
  <div class="service abs" style="left:125px">
    <svg width="70" height="70" viewBox="0 0 70 70" fill="none" stroke="#333" stroke-width="3"><path d="M20 12h9l4 12-6 4a30 30 0 0 0 15 15l4-6 12 4v9c0 3-2 5-5 5A42 42 0 0 1 15 17c0-3 2-5 5-5z"/><path d="M42 10h16M42 10l6 6M42 10l6-6"/></svg>
    <h3>Answering Enquiries,<br>Check-Ins / Outs</h3>
    <p>We will answer all guest's enquiries,<br>meet them to handover key and<br>verification check.We also provide<br>24hr on-call support.</p>
  </div>
  <div class="divider abs" style="left:425px"></div>
  <div class="service abs" style="left:445px">
    <svg width="70" height="70" viewBox="0 0 70 70" fill="none" stroke="#333" stroke-width="3"><path d="M16 6l14 30"/><path d="M24 36h14l4 10H20z" fill="#333"/><rect x="40" y="40" width="20" height="24" rx="5"/><path d="M46 40v-6h8"/></svg>
    <h3>Cleaning, Laundry<br>and Maintenance</h3>
    <p>We get the professional cleaning team<br>to clean up the place after the guest<br>checked-out every time.</p>
  </div>
  <div class="divider abs" style="left:775px"></div>
  <div class="service abs" style="left:775px">
    <svg width="80" height="70" viewBox="0 0 80 70" fill="none" stroke="#333" stroke-width="3"><rect x="6" y="10" width="68" height="50"/><path d="M6 20h68"/><path d="M16 48l14-12 10 8 16-16 10 6"/></svg>
    <h3>Marketing &amp;<br>Optimization</h3>
    <p>We take professional photos and write<br>persuasive copywriting to optimize<br>your listing in order to get<br>more booking.</p>
  </div>
</section>

<div class="section-title steps-title abs"><div class="rule"></div><h2>How to start?</h2><p>The following steps are required in<br>order to get your place ready to start.</p></div>

<div class="step abs" style="left:125px"><div class="step-num">01</div><div class="rule"></div><div class="step-label">Getting the<br>required items</div></div>
<div class="step abs" style="left:375px"><div class="step-num">02</div><div class="rule"></div><div class="step-label">Renovation &amp;<br>Furnishing</div></div>
<div class="step abs" style="left:625px"><div class="step-num">03</div><div class="rule"></div><div class="step-label">Sign a management<br>agreement</div></div>
<div class="step abs" style="left:875px"><div class="step-num">04</div><div class="rule"></div><div class="step-label">Handover Keys &amp; Access cards, and relevant information</div></div>
<svg class="abs" style="left:0;top:2200px" width="1200" height="30" viewBox="0 0 1200 30" fill="none" stroke="#ee3a46" stroke-width="2">
  <path d="M331 15h38M361 9l8 6-8 6"/>
  <path d="M581 15h38M611 9l8 6-8 6"/>
  <path d="M831 15h38M861 9l8 6-8 6"/>
</svg>

<section class="packages abs">
  <div class="section-title abs" style="top:70px"><div class="rule"></div><h2>Packages</h2></div>
  <div class="card abs" style="left:145px">
    <div class="price">RM7,950.00</div>
    <h3>Economic Package</h3>
    <ul><li>Full Height Day &amp; Night curtain</li><li>Main Entrance Door Grill</li><li>Supply &amp; Install LED Surface Light</li><li>Supply &amp; Install Down Light</li><li>Supply &amp; Install Ceiling Fan</li><li>Retractive Hanging Rack</li></ul>
  </div>
  <div class="card abs" style="left:457px">
    <div class="price">RM27,000.00</div>
    <h3>F.O.C</h3>
    <ul><li>ID drawing &amp; project management fee</li><li>Defect checking and follow up</li><li>After renovation cleaning</li><li>Stainless steel drying rack at yard</li></ul>
  </div>
  <div class="card abs" style="left:770px">
    <div class="price">RM7,950.00</div>
    <h3>Furniture Package</h3>
    <ul><li>Sofa bed</li><li>Coffee table</li><li>Dining table set with 6 seaters</li><li>Microfiber pillows</li><li>Carpet rug</li><li>Study table &amp; chairs</li></ul>
  </div>
  <a class="btn abs" href="#">View all packages</a>
</section>

<section class="banner abs" role="img" aria-label="Warmly lit lounge with armchairs, lamps and bookshelves"></section>
<div class="banner-copy abs" style="top:3288px">
  <h2>Well maintain house condition.</h2>
  <p>Cleaning is the No.1 priority to ensure the guests' staying experience,<br>so all units are always in tip-top condition to gain 5-stars rating.</p>
  <a class="btn" href="#">Read more</a>
</div>

<div class="footer-line abs"></div>
<footer class="site-footer abs">
  <div class="brand abs">Meadow Kr Circle</div>
  <div class="f-col abs" style="left:483px;width:240px">
    <h4>CONTACT US</h4>
    <div class="f-row"><svg width="10" height="13" viewBox="0 0 10 13"><path d="M5 0a5 5 0 0 0-5 5c0 4 5 8 5 8s5-4 5-8a5 5 0 0 0-5-5z" fill="#fff"/></svg><span>L12-03 Seroja Court, Jalan Kenanga,<br>Taman Melor, 81200 Johor Bahru.</span></div>
    <div class="f-row"><svg width="11" height="11" viewBox="0 0 24 24"><path d="M6.6 10.8a15 15 0 0 0 6.6 6.6l2.2-2.2c.3-.3.7-.4 1-.2 1.1.4 2.3.6 3.6.6.6 0 1 .4 1 1V20c0 .6-.4 1-1 1A17 17 0 0 1 3 4c0-.6.4-1 1-1h3.5c.6 0 1 .4 1 1 0 1.3.2 2.5.6 3.6.1.3 0 .7-.2 1z" fill="#fff"/></svg><span>+60 7 555 0142</span></div>
    <div class="f-row"><svg width="12" height="10" viewBox="0 0 12 10"><rect width="12" height="10" fill="#fff"/><path d="M0 0l6 5 6-5" stroke="#262626" fill="none"/></svg><span>info@meadowkrcircle.example</span></div>
  </div>
  <div class="f-col abs" style="left:773px">
    <h4>MENU</h4>
    <div>Home<br>About us<br>Services<br>Explore the Place<br>Blog<br>Contact Us</div>
  </div>
  <div class="f-col abs" style="left:940px">
    <h4>CONNECT WITH US</h4>
    <div class="social-row"><span></span>Chatterly</div>
    <div class="social-row"><span></span>Pinwheel</div>
    <div class="social-row"><span></span>Linkway</div>
  </div>
  <div class="f-rule abs"></div>
  <div class="copyright abs">Copyrights @ 2018 All Rights Reserved</div>
</footer>

</body>
</html>
```